Flyer für Schulungen für Unternehmen
Zielgruppe
Wir machen Schulungen für Unternehmen zum Thema Logistik, Arbeitsmittelprüfung und Betriebssicherheit.
Aufgabenstellung
Wir haben eine neue Förderung erhalten für unsere Weiterbildung nach dem BKrFQG.
Wir können nun Schulungen ab 40€ abieten und wollen dafür Werbung gestalten. Wir möchten einen Fyler nur zum Thema Schulungen bei der Kolbe Academy.

```html
<!DOCTYPE html>
<html lang="de">
<head>
<meta charset="utf-8">
<title>Kolbe Academy – Schulungsflyer</title>
<link href="https://fonts.googleapis.com/css2?family=Jost:wght@300;400;500;600;700&family=League+Spartan:wght@700;800&display=swap" rel="stylesheet">
<style>
  :root{
    --bg:#e8e1d7;
    --paper:#f4f4f3;
    --ink:#1b1b1b;
    --black:#0c0c0c;
    --dark:#505050;
    --mid:#bdbdbd;
    --light:#d8d8d8;
    --pale:#e6e6e6;
    --green:#6cc04a;
    --white:#ffffff;
    --badge-shape:#d4d4d4;
  }
  *{box-sizing:border-box;margin:0;padding:0}
  html,body{width:1200px;height:1107px;overflow:hidden;background:var(--bg)}
  body{font-family:"Jost",sans-serif;color:var(--ink);display:flex;align-items:center;justify-content:center}
  .flyer{width:1110px;height:800px;display:grid;grid-template-columns:370px 370px 370px;background:var(--paper);box-shadow:0 18px 40px rgba(0,0,0,.18);position:relative}
  .panel{position:relative;overflow:hidden;display:flex;flex-direction:column}
  .course{position:relative;padding:22px 26px 0 26px}
  .course-head{display:flex;align-items:flex-end;gap:12px;border-bottom:1px solid currentColor;padding-bottom:6px}
  .course-num{font-family:"League Spartan",sans-serif;font-weight:800;font-size:50px;line-height:.8}
  .course-title{font-weight:600;font-size:17px;line-height:1.15}
  .course-price{font-size:11.5px;font-weight:400;margin:6px 0 8px 0;padding-bottom:4px;border-bottom:1px solid currentColor;display:inline-block}
  .course-body{font-size:11.5px;line-height:1.35;font-weight:400}
  .course-body b{font-weight:600}
  .course-body ul{list-style:none;padding-left:12px}
  .course-body li::before{content:"- "}
  .indent{padding-left:22px}
  .num-right{position:absolute;right:22px;top:18px}
  .sec-7{background:var(--paper);height:345px}
  .sec-8{background:var(--dark);color:var(--white);height:330px}
  .sec-9{background:var(--black);color:var(--white);height:315px}
  .sec-10{background:var(--light);height:180px}
  .sec-11{background:var(--mid);height:180px}
  .sec-12-left{background:var(--paper);height:125px}
  .sec-12-mid{background:var(--pale);height:125px}
  .sec-12{position:absolute;left:26px;bottom:60px;width:690px;display:flex;align-items:flex-end;gap:14px}
  .sec-12-items{position:absolute;left:26px;bottom:30px;width:700px;height:0}
  .item-l{position:absolute;left:0;top:-18px;font-size:11.5px}
  .item-r{position:absolute;left:370px;top:-18px;font-size:11.5px}
  .cover-photo{height:200px;background:linear-gradient(135deg,#4c5660 0%,#7b8590 40%,#d9893a 62%,#5d6670 100%)}
  .brand{display:flex;flex-direction:column;align-items:center;padding:28px 20px 14px}
  .brand-name{font-weight:700;font-size:34px;letter-spacing:.5px;color:var(--green);display:flex;align-items:center;gap:10px}
  .brand-dot{width:14px;height:14px;border-radius:50%;background:var(--green)}
  .brand-claim{font-size:11.5px;text-align:center;line-height:1.35;margin-top:18px;padding:0 24px}
  .brand-claim b{font-weight:600}
  .offer{background:var(--pale);padding:22px 22px 0;height:250px;position:relative}
  .offer-text{font-weight:500;font-size:15px;text-align:center;line-height:1.25}
  .box{position:absolute;background:var(--green);color:var(--white);text-align:center;display:flex;flex-direction:column;justify-content:center;align-items:center}
  .box-frame{position:absolute;border:1.5px solid var(--ink)}
  .box small{font-size:11px;font-weight:300;line-height:1.25}
  .box strong{font-weight:500;font-size:38px;line-height:1.1}
  .badge{position:absolute;background:var(--white);border:1px solid #cfcfcf;display:flex;align-items:center;justify-content:center}
  .badge-shape{background:var(--badge-shape)}
  .badge-funding .badge-shape{width:30px;height:30px}
  .badge-cofunding .badge-shape{width:46px;height:30px}
  .contact{background:var(--dark);color:var(--white);flex:1;padding:60px 40px 0 80px;font-size:12px;font-weight:300;line-height:1.8}
  .contact div{display:flex;align-items:center;gap:10px}
  .contact svg{width:12px;height:12px;fill:var(--white)}
</style>
</head>
<body>
<main class="flyer">

  <section class="panel">
    <article class="course sec-7">
      <div class="course-head"><span class="course-num">7</span><h2 class="course-title">Sicherer Umgang mit Flurförderzeugen</h2></div>
      <p class="course-price">effektiv ab 69€ netto p. P.*</p>
      <div class="course-body">
        <p>Gabelstaplerschein</p>
        <p><b>Dauer:</b> 8 bis 16 Stunden – Theorie und Praxis</p>
        <div class="indent">
          <p><b>Theoretischer Teil:</b></p>
          <ul>
            <li>Erklärung der Vorschriften der Berufsgenossenschaft beim Einsatz von Flurförderzeugen</li>
            <li>Unfallverhütungsvorschrift</li>
            <li>Kontrolle bei Arbeitsbeginn</li>
            <li>Schriftliche Prüfung</li>
          </ul>
          <p><b>Praktischer Teil:</b></p>
          <ul>
            <li>Tägliche Sicht- und Funktionsprüfung vor Fahrtantritt</li>
            <li>Fahrübungen</li>
            <li>Durchführung eines Arbeitsspieles</li>
            <li>Praktische Prüfung im Parcours</li>
          </ul>
        </div>
      </div>
    </article>
    <article class="course sec-8">
      <span class="course-num num-right">8</span>
      <div class="course-head" style="margin-top:36px"><h2 class="course-title">Sicherer Umgang mit Kranen</h2></div>
      <div class="course-body" style="margin-top:10px">
        <p>Kranschein - alle Flur &amp; Kanzelgesteuerte Krane, Hallen- und Portalkrane</p>
        <p><b>Dauer:</b> 8-16 Stunden – Theorie und Praxis</p>
        <ul class="indent">
          <li>Gesetzliche Vorschriften und Vorgaben der Berufsgenossenschaft</li>
          <li>Unfallverhütungsvorschriften, Bedienungsvorschriften</li>
          <li>Sicherheitsregeln, persönliche Schutzausrüstungen</li>
          <li>Umgang mit Lasten, Arbeit mit Traglasttabellen</li>
          <li>Einweisung / Handzeichengebung</li>
          <li>Anforderungen an die Kranabnahme und -prüfung</li>
          <li>Pflege- und Wartung, Sichtkontrollen und Funktionsproben</li>
          <li>Verhalten bei Störungen</li>
          <li>Praktische Übungen</li>
          <li>Theorieprüfung und praktischer Einzeltest</li>
        </ul>
      </div>
    </article>
    <div class="sec-12-left"></div>
  </section>

  <section class="panel">
    <article class="course sec-9">
      <span class="course-num num-right">9</span>
      <div class="course-head" style="margin-top:36px"><h2 class="course-title">Unterweisung Ladungssicherung</h2></div>
      <p class="course-price">effektiv ab 69€ netto p. P.*</p>
      <div class="course-body">
        <p><b>Dauer:</b> 8 Stunden – Theorie</p>
        <p>Ordnungsgemäße Ladungssicherung führt zur Reduzierung von Transportschäden, Reduzierung von Unfall- und Folgekosten, sowie Vermeidung von Bußgeldern.</p>
        <ul class="indent" style="margin-top:6px;padding-left:10px">
          <li>Rechtliche Grundlagen</li>
          <li>Verordnung sowie Richtlinien zur Ladungssicherung</li>
          <li>Physikalische Grundlagen</li>
          <li>Ladungssicherung bei Fahrzeugen mit offener Ladefläche</li>
          <li>Ladungssicherung bei Handwerker- und Werkstattfahrzeugen</li>
          <li>Ladungssicherung bei Fahrzeugen mit Kastenaufbau</li>
          <li>Ladungssicherung im Kurier-, Express-, Paketdienst</li>
        </ul>
      </div>
    </article>
    <article class="course sec-10">
      <div class="course-head"><span class="course-num">10</span><h2 class="course-title">Jährliche Unterweisung Flurförderzeug</h2></div>
      <div class="course-body" style="margin-top:8px">
        <p><b>Dauer:</b> 4-8 Stunden – Theorie</p>
        <ul>
          <li>Erklärung der Vorschriften der Berufsgenossenschaft beim Einsatz von Flurförderzeugen</li>
          <li>Techniken von Flurförderzeugen allgemein</li>
          <li>Unfallverhütungsvorschrift</li>
          <li>Kontrolle bei Arbeitsbeginn</li>
        </ul>
      </div>
    </article>
    <article class="course sec-11">
      <span class="course-num num-right">11</span>
      <div class="course-head" style="margin-top:36px"><h2 class="course-title">Jährliche Unterweisung Kran</h2></div>
      <div class="course-body" style="margin-top:8px">
        <p>Unterweisung Kran - alle Flur &amp; kanzelgesteuerte Krane, Hallen- und Portalkrane</p>
        <p><b>Dauer:</b> 4-8 Stunden - Theorie</p>
      </div>
    </article>
    <div class="sec-12-mid"></div>
  </section>

  <section class="panel">
    <div class="cover-photo" role="img" aria-label="Foto: zwei Lagerarbeiter mit Schutzhelm und Warnweste an einem Gabelstapler"></div>
    <div class="brand">
      <div class="brand-name"><span class="brand-dot"></span>KOLBE ACADEMY</div>
      <p class="brand-claim">Ihr Experte für Seminare und Schulungen rund um die <b>Logistik</b> und <b>Arbeitsmittelprüfungen</b> nach Betriebssicherheitsverordnung</p>
    </div>
    <div class="offer">
      <p class="offer-text">Sichern Sie sich jetzt mit unseren Fachkursen in Talheim die Bildungsförderung mit einem Zuschuss von bis zu 70%!</p>
      <div class="box-frame" style="left:20px;top:122px;width:150px;height:118px"></div>
      <div class="box" style="left:30px;top:112px;width:150px;height:118px"><small>mit einem Zuschuss<br>von bis zu</small><strong>70%</strong></div>
      <div class="box-frame" style="left:200px;top:92px;width:135px;height:118px"></div>
      <div class="box" style="left:210px;top:102px;width:135px;height:118px"><small>ab</small><strong>40€</strong><small>netto p. P.*</small></div>
      <div class="badge badge-funding" style="left:118px;top:212px;width:92px;height:62px" role="img" aria-label="Platz für Förderlogo"><span class="badge-shape"></span></div>
      <div class="badge badge-cofunding" style="left:218px;top:195px;width:110px;height:62px" role="img" aria-label="Platz für Kofinanzierungslogo"><span class="badge-shape"></span></div>
    </div>
    <div class="contact">
      <div><svg viewBox="0 0 12 12"><circle cx="6" cy="6" r="5" fill="none" stroke="#fff" stroke-width="1"/><path d="M1 6h10M6 1v10" stroke="#fff" stroke-width=".8"/></svg>kolbeacademy.de/</div>
      <div><svg viewBox="0 0 12 12"><path d="M2 1l2.5 0 1 3-1.5 1c.7 1.4 1.6 2.3 3 3l1-1.5 3 1V11C5.5 11 1 6.5 1 2z"/></svg>07000 - 4815 - 62</div>
      <div><svg viewBox="0 0 12 12"><rect x="1" y="2.5" width="10" height="7" fill="none" stroke="#fff" stroke-width="1"/><path d="M1 2.5l5 4 5-4" fill="none" stroke="#fff" stroke-width="1"/></svg>jana.roth@kolbe-academy.de</div>
    </div>
  </section>

  <div class="sec-12">
    <span class="course-num">12</span>
    <h2 class="course-title">Prüfungen von Arbeitsmitteln nach BetrSichV /<br>wiederkehrende Sicht- und Funktionsprüfungen nach DGUV</h2>
  </div>
  <div class="sec-12-items">
    <p class="item-l">- Herstellerunabhängige Prüfung von Leitern und Tritten</p>
    <p class="item-r">- Herstellerunabhängige Regalinspektion und Regalprüfung</p>
  </div>
</main>
</body>
</html>
```